Webdesign für Full-Service-Internetagentur
Zielgruppe
Falkenhainer Webdesign – Ihr Partner für außergewöhnliche Onlinepräsenzen
Wir bieten seit mehr als 16 Jahren Internetauftritte für kleine und mittelständische Unternehmen an.
Als Full-Service-Internetagentur liefern wir Ihnen individuelle auf Ihre Bedürfnisse, Ihre Branche und Ihre Zielgruppe zugeschnittene Lösungen für Ihre Onlinepräsentation an. Unser Angebot beinhaltet sowohl ein ideenreiches Webdesign kombiniert mit den aktuellsten Grundsätzen für Web-Programmierung als auch die Unterstützung für Ihr erfolgreiches Werben im Internet.
Eine gute Beratung heißt für uns genau hinhören und verstehen, was Sie wirklich brauchen. Je besser wir Ihre Ziele kennen, desto besser können wir Ihre Onlinepräsenz umsetzen. Unsere Kundenberater erläutern Ihnen persönlich mit Enthusiasmus die verschiedenen Möglichkeiten der Darstellung Ihrer Firma im Internet und entwickeln Konzepte, die Ihren Anforderungen bestmöglich entsprechen. Nicht nur während der Projektphase, sondern auch nach Onlinestellung Ihrer Internetseite stehen wir Ihnen mit persönlicher Kundenbetreuung und Supportdienstleistungen zur Verfügung.
Aufgabenstellung
siehe : https://www.falkenhainer-webdesign.example/

```html
<!DOCTYPE html>
<html lang="de">
<head>
<meta charset="utf-8">
<title>Falkenhainer Webdesign</title>
<link href="https://fonts.googleapis.com/css2?family=Poppins:wght@400;500;600;700&family=Roboto:wght@400;500;700&display=swap" rel="stylesheet">
<style>
:root{
  --red:#e53a3f;
  --red-band:#ec3e45;
  --ink:#1d1d1f;
  --text:#555;
  --muted:#a9a9a9;
  --line:#e2e2e2;
  --grey-bg:#f3f3f3;
  --foot-bg:#ececec;
}
*{margin:0;padding:0;box-sizing:border-box}
html,body{width:1200px;height:2856px;overflow:hidden;background:#fff}
body{position:relative;font-family:"Roboto",sans-serif;color:var(--ink)}
.abs{position:absolute}
.poppins{font-family:"Poppins",sans-serif}

/* header */
.site-header{position:absolute;left:0;top:0;width:1200px;height:114px;background:#fff}
.brand{left:233px;top:42px;font-family:"Poppins",sans-serif;font-size:20px;color:var(--ink)}
.phone{left:848px;top:29px;font-family:"Poppins",sans-serif;font-size:13px;color:var(--red);display:flex;align-items:center;gap:6px}
.nav{left:547px;top:58px;display:flex;gap:0;font-family:"Poppins",sans-serif;font-size:12px;font-weight:500}
.nav a{color:var(--ink);text-decoration:none;margin-right:18px}
.nav a.active{color:var(--red);margin-right:26px}
.partner-badge{left:1126px;top:9px;width:58px;height:97px;background:#8f1b1e;border-top:46px solid #e6e6e6}

/* hero */
.hero{left:0;top:114px;width:1200px;height:424px;background:linear-gradient(120deg,#d8dde2 0%,#b8a49a 35%,#8a6f63 55%,#c7b5a8 80%,#e8e4e0 100%)}
.hero-box{left:236px;top:216px;width:354px;height:158px;background:rgba(255,255,255,.82)}
.hero-title{left:246px;top:235px;font-family:"Poppins",sans-serif;font-weight:700;font-size:33px;line-height:31px;color:#111}
.hero-sub{left:246px;top:309px;font-family:"Poppins",sans-serif;font-size:13px;color:#222}
.btn-red{background:var(--red);color:#fff;font-family:"Poppins",sans-serif;font-size:9px;font-weight:600;display:flex;align-items:center;justify-content:center;gap:6px;letter-spacing:.3px}
.hero-btn{left:248px;top:327px;width:116px;height:30px}
.slide-dots{left:57px;top:150px;width:2px;height:70px;border-left:2px dotted #fff}
.hero-base{left:0;top:416px;width:1200px;height:8px;background:#cfcfcf}

/* intro */
.intro{left:0;top:538px;width:1200px;height:610px;background:linear-gradient(#fff 0%,#fff 40%,#f7eded 100%)}
.deco-letter{font-family:"Poppins",sans-serif;font-weight:700;color:#f4f4f4;line-height:1}
.intro .deco-letter{left:30px;top:60px;font-size:180px}
.intro-title{left:233px;top:84px;font-family:"Poppins",sans-serif;font-weight:500;font-size:23px;line-height:35px;color:#111}
.intro-text{left:609px;top:82px;width:350px;font-family:"Poppins",sans-serif;font-size:10.5px;line-height:21px;color:#888}
.intro-text p+p{margin-top:8px}
.card{top:316px;width:231px;height:217px;background:#fff;text-align:center;padding-top:52px}
.card svg{display:block;margin:0 auto}
.card h3{font-family:"Poppins",sans-serif;font-weight:500;font-size:13px;margin-top:20px;color:#111}
.card p{font-family:"Poppins",sans-serif;font-size:10.5px;line-height:19px;color:var(--muted);margin:4px 18px 0}

/* claim band */
.claim{left:0;top:1148px;width:1200px;height:205px;background:var(--red-band)}
.claim h2{position:absolute;left:0;top:69px;width:1200px;text-align:center;font-family:"Poppins",sans-serif;font-weight:600;font-size:23px;color:#fff}
.claim .btn-outline{position:absolute;left:534px;top:127px;width:130px;height:32px;border:1px solid #fff;color:#fff;font-family:"Poppins",sans-serif;font-size:9px;font-weight:600;display:flex;align-items:center;justify-content:center;gap:6px}

/* references */
.refs{left:0;top:1353px;width:1200px;height:596px;background:#fff}
.refs .deco-letter{left:72px;top:28px;font-size:160px}
.label{font-family:"Poppins",sans-serif;font-size:9.5px;font-weight:500;letter-spacing:.4px}
.label.red{color:var(--red)}
.label.grey{color:#999}
.sec-title{font-family:"Poppins",sans-serif;font-weight:500;font-size:24px;line-height:34px;color:#111}
.rule{width:32px;height:2px;background:var(--red)}
.btn-ghost{font-family:"Poppins",sans-serif;font-size:9px;font-weight:500;display:flex;align-items:center;justify-content:center;color:#111}
.tag{left:462px;top:171px;width:171px;height:23px;background:var(--red);color:#fff;font-family:"Poppins",sans-serif;font-size:11px;display:flex;align-items:center;justify-content:center}
.tag::after{content:"";position:absolute;left:80px;bottom:-5px;border:5px solid transparent;border-top-color:var(--red);border-bottom:0}
.showcase{left:235px;top:211px;width:728px;height:351px;background:linear-gradient(180deg,#e9e6e4 0%,#cfc9c6 50%,#e2e2e2 100%);border-radius:6px}

/* news */
.news{left:0;top:1949px;width:1200px;height:267px;background:var(--grey-bg)}
.news-col{top:144px;width:227px}
.news-col .date{font-size:8.5px;color:#777;padding-bottom:7px;border-bottom:1px solid var(--line)}
.news-col h4{font-size:10.5px;font-weight:500;line-height:15px;margin-top:10px;color:#222}
.news-col p{font-size:9.5px;line-height:16px;color:#666;margin-top:8px}
.news-col a{display:block;font-size:9.5px;color:var(--red);margin-top:10px;text-decoration:none}

/* contact */
.contact{left:0;top:2216px;width:1200px;height:468px;background:#fff}
.field{border:1px solid #ddd;background:#fff;font-size:8.5px;color:#888;padding:10px 11px}
.consent{left:267px;top:305px;width:335px;font-size:8px;line-height:14px;color:#444}
.consent a{color:var(--red);text-decoration:none}
.checkbox{left:234px;top:305px;width:20px;height:20px;border:1px solid #ccc}
.submit{left:241px;top:379px;width:123px;height:26px;background:var(--red);border-radius:13px;color:#fff;font-size:8.5px;font-weight:500;display:flex;align-items:center;justify-content:center}

/* footer */
.footer{left:0;top:2684px;width:1200px;height:133px;background:#fff}
.footer h5{font-size:10.5px;font-weight:500;color:var(--red);letter-spacing:.3px}
.footer .links{font-size:9.5px;line-height:19px;color:#333}
.footer a{color:var(--red);text-decoration:none}
.copyright{left:0;top:2817px;width:1200px;height:39px;background:var(--foot-bg);font-size:9px;color:#333;padding:12px 0 0 234px}
.copyright span{color:var(--red)}
</style>
</head>
<body>

<header class="site-header">
  <div class="abs brand">Falkenhainer Webdesign</div>
  <div class="abs phone">
    <svg width="20" height="20" viewBox="0 0 24 24" fill="none" stroke="#e53a3f" stroke-width="1.6"><path d="M5 3h4l2 5-2.5 1.5a11 11 0 0 0 6 6L16 13l5 2v4a2 2 0 0 1-2 2A17 17 0 0 1 3 5a2 2 0 0 1 2-2z"/></svg>
    0341 – 5550180
  </div>
  <nav class="abs nav">
    <a class="active">Die Agentur</a><a>Referenzen</a><a>Engagement</a><a style="margin-right:24px">Aktuelles</a><a style="margin-right:20px">Kontakt</a><a>FAQ</a>
  </nav>
  <div class="abs partner-badge" role="img" aria-label="Partner-Siegel"></div>
</header>

<section class="abs hero" role="img" aria-label="Foto: Team arbeitet gemeinsam an einem Bildschirm">
  <div class="abs slide-dots"></div>
  <div class="abs hero-box"></div>
  <h1 class="abs hero-title">Lasst uns beginnen<br>Zusammenarbeiten</h1>
  <p class="abs hero-sub">Wir bieten Ihnen alle Arten von Online-Diensten</p>
  <div class="abs btn-red hero-btn">WEITERLESEN <svg width="12" height="8" viewBox="0 0 12 8" fill="none" stroke="#fff" stroke-width="1.2"><path d="M0 4h11M8 1l3 3-3 3"/></svg></div>
  <div class="abs hero-base"></div>
</section>

<section class="abs intro">
  <div class="abs deco-letter">W</div>
  <h2 class="abs intro-title">Wir sind dynamisch<br>Team von kreativen Menschen<br>der Innovation<br>&amp; Entwicklungskompetenz.</h2>
  <div class="abs intro-text">
    <p>Wir bieten Web- und Entwicklungsservices für Startups und kleine Unternehmen, um einen Partner für ihre Anforderungen in den Bereichen digitale Medien, Designentwicklung, Lead-Generierung und Kommunikation zu suchen. Wir arbeiten mit Ihnen, nicht für Sie. Obwohl wir große Ressourcen haben.</p>
    <p>Wir haben unseren Hauptsitz in Deutschland, um einen Kunden bestmöglich bedienen zu können Basis, die sich weltweit erstreckt.</p>
  </div>

  <div class="abs card" style="left:110px">
    <svg width="46" height="44" viewBox="0 0 46 44" fill="none" stroke="#e53a3f" stroke-width="1.5"><path d="M4 42V14l6-12 6 12v28zM4 14h12M10 14v28"/><rect x="22" y="2" width="20" height="40"/><path d="M22 9h7M22 16h10M22 23h7M22 30h10M22 37h7"/></svg>
    <h3>Konzeption &amp; Beratung</h3>
    <p>Wir entwickeln Ihr individuelles Konzept und begleiten Sie über die Fertigstellung hinaus.</p>
  </div>
  <div class="abs card" style="left:359px">
    <svg width="58" height="44" viewBox="0 0 58 44" fill="none" stroke="#e53a3f" stroke-width="1.5"><rect x="14" y="2" width="42" height="28"/><path d="M14 24h42"/><rect x="2" y="18" width="16" height="24" rx="2"/><path d="M2 36h16M30 8l6 6M36 8v6h-6M44 20l-6-6"/></svg>
    <h3>Webdesign &amp; Programmierung</h3>
    <p>Wir setzen Ihre individuell gestaltete Webseite mittels aktueller Web-Technologien um.</p>
  </div>
  <div class="abs card" style="left:609px">
    <svg width="46" height="46" viewBox="0 0 46 46" fill="none" stroke="#e53a3f" stroke-width="1.5"><circle cx="23" cy="23" r="21"/><path d="M8 32l10-10 6 6 12-12M30 16h6v6"/></svg>
    <h3 style="margin-top:18px">Online Marketing</h3>
    <p>Wir analysieren Ihre Webseite und schaffen Voraussetzungen für ein optimales Suchmaschinen-Ranking.</p>
  </div>
  <div class="abs card" style="left:856px">
    <svg width="44" height="42" viewBox="0 0 44 42" fill="none" stroke="#e53a3f" stroke-width="1.5"><rect x="2" y="2" width="40" height="38"/><path d="M2 10h40M6 6h2M10 6h2M14 6h2"/><text x="12" y="31" font-family="Poppins,sans-serif" font-size="13" fill="#e53a3f" stroke="none">.de</text></svg>
    <h3 style="margin-top:22px">Domain &amp; Webhosting</h3>
    <p>Alles was Sie für Ihr Webprojekt brauchen.</p>
  </div>
</section>

<section class="abs claim">
  <h2>Ehrlich. Streßerprobt. Verständlich. Erfolgreich.</h2>
  <div class="btn-outline">ANGEBOT EINHOLEN <svg width="12" height="8" viewBox="0 0 12 8" fill="none" stroke="#fff" stroke-width="1.2"><path d="M0 4h11M8 1l3 3-3 3"/></svg></div>
</section>

<section class="abs refs">
  <div class="abs deco-letter">R</div>
  <div class="abs label red" style="left:234px;top:48px">REFERENCES</div>
  <h2 class="abs sec-title" style="left:233px;top:71px">Wir haben viel Arbeit geleistet Überprüfen<br>Sie einige von hier</h2>
  <div class="abs rule" style="left:234px;top:149px"></div>
  <div class="abs btn-ghost" style="left:841px;top:118px;width:125px;height:30px;border:1px solid #ddd">SIEHE ALLE PROJEKTE</div>
  <div class="abs tag">Maurerbetrieb Steinfeld</div>
  <div class="abs showcase" role="img" aria-label="Referenzprojekt auf Monitor, Tablet, Smartphone und Laptop"></div>
</section>

<section class="abs news">
  <div class="abs label grey" style="left:234px;top:40px">NACHRICHTEN</div>
  <h2 class="abs sec-title" style="left:234px;top:55px">Was es neues gibt</h2>
  <div class="abs rule" style="left:234px;top:97px"></div>
  <div class="abs btn-ghost" style="left:805px;top:44px;width:161px;height:30px;background:#e4e4e4">ALLE NACHRICHTEN ANZEIGEN</div>

  <div class="abs news-col" style="left:234px">
    <div class="date">May 10, 2019</div>
    <h4>"Für jeden" ETWAS bei Falkenhainer Webdesign</h4>
    <p>Falkenhainer Webdesign kann einen weiteren neuen Kunden begrüßen!</p>
    <a>Weiterlesen</a>
  </div>
  <div class="abs news-col" style="left:487px">
    <div class="date">JULI 108, 2019</div>
    <h4>Malerprojekt Falkenhain GmbH</h4>
    <p>Neue Website für die Malerprojekt Falkenhain GmbH</p>
    <a>Weiterlesen</a>
  </div>
  <div class="abs news-col" style="left:740px">
    <div class="date">JANUAR 16, 2019</div>
    <h4>ACHTUNG - eingeschränkten Verfügbarkeit von HostedMail-Konten</h4>
    <p>Aktuelle Systemmeldungen DomainHafen</p>
    <a>Weiterlesen</a>
  </div>
</section>

<section class="abs contact">
  <h2 class="abs poppins" style="left:234px;top:40px;font-size:20px;font-weight:500">Wir haben Ihr Interesse geweckt?</h2>
  <div class="abs field" style="left:234px;top:85px;width:176px;height:33px">Name *</div>
  <div class="abs field" style="left:421px;top:85px;width:177px;height:33px">Firma</div>
  <div class="abs field" style="left:234px;top:123px;width:176px;height:33px">Straße, Nr.</div>
  <div class="abs field" style="left:421px;top:123px;width:177px;height:33px">PLZ, Ort</div>
  <div class="abs field" style="left:234px;top:160px;width:176px;height:33px">Telefon *</div>
  <div class="abs field" style="left:421px;top:160px;width:177px;height:33px">E-Mail *</div>
  <div class="abs field" style="left:234px;top:198px;width:364px;height:83px">Ihre Nachricht an uns *</div>
  <div class="abs checkbox"></div>
  <p class="abs consent">Ich habe die Datenschutzerklärung zur Kenntnis genommen. Ich stimme zu, dass meine Angaben und Daten zur Beantwortung meiner Anfrage elektronisch erhoben und gespeichert werden. Hinweis: Sie können Ihre Einwilligung jederzeit für die Zukunft per E-Mail an <a>info@falkenhainer-webdesign.example</a> widerrufen.</p>
  <div class="abs submit">FORMULAR ABSCHICKEN</div>

  <div class="abs label grey" style="left:673px;top:44px">KONTAKTIERE UNS</div>
  <h2 class="abs poppins" style="left:673px;top:69px;font-size:21px;font-weight:500;line-height:35px">Zögern Sie nicht<br>Kontaktieren Sie uns für alle<br>Art von Informationen</h2>
  <div class="abs rule" style="left:674px;top:180px;width:30px"></div>
  <p class="abs poppins" style="left:673px;top:203px;width:300px;font-size:12.5px;line-height:15px;color:#999">Rufen Sie uns zur sofortigen Unterstützung diese Nummer an</p>
  <p class="abs poppins" style="left:673px;top:237px;font-size:19px;font-weight:500">0341 - 5550180</p>
</section>

<footer class="abs footer">
  <h5 class="abs" style="left:234px;top:20px">NAVIGATION</h5>
  <div class="abs links" style="left:234px;top:38px">Portfolio<br>Die Agentur<br>Referenzen<br>Aktuelles</div>
  <div class="abs links" style="left:318px;top:38px">Kontakt<br>FAQ<br>Impressum<br>Datenschutz</div>
  <h5 class="abs" style="left:466px;top:20px">KONTAKT</h5>
  <div class="abs links" style="left:466px;top:38px">Falkenhainer Webdesign<br>Inh. Lena Hartwig<br>Lindenallee 12<br>09120 Falkenhain</div>
  <div class="abs links" style="left:654px;top:38px">Fon: 0341 - 5550180<br>Fax: 0341 - 5550190<br><a>info@falkenhainer-webdesign.example</a></div>
</footer>

<div class="abs copyright">© 2019 by <span>Falkenhainer Webdesign</span></div>

</body>
</html>
```